Custom Woodworking and Rock Design

We specialize in original, high quality, wood and rock art. It’s should be self explanatory ask questions if you need. Your team designing a logo. Furniture is custom made to order. Rocks are designed depending on consumer needs. Wood and rock can also be combined for custom work. Painted rocks on vintage wood. Custom chairs and cabinets. Artistic rocks for multiple uses:garden, magnets, custom. All ideas and requests are welcome.

Target Market(s)

All

Contact Information for Business Card

Mara Voss
Talbertstonecraft@mailbrook.net

Font styles to use
Sans Serif

Requirements
Must have
• Clear lettering
Nice to have
• Eye catching
Should not have
• Blurr

```html
<!DOCTYPE html>
<html lang="en">
<head>
<meta charset="utf-8">
<title>Talbert Stonecraft — Business Card</title>
<link href="https://fonts.googleapis.com/css2?family=Lato:wght@400;700&display=swap" rel="stylesheet">
<style>
  :root {
    --bg: #d9d4cc;
    --card: #efefee;
    --card-edge: #dcdcdb;
    --brand-grey: #7b7b7b;
    --brand-brown: #5b4a42;
    --ink: #3f3b39;
    --icon: #4a4240;
  }
  * { margin: 0; padding: 0; box-sizing: border-box; }
  html, body { width: 1200px; height: 939px; overflow: hidden; }
  body {
    background: var(--bg);
    font-family: "Lato", sans-serif;
    position: relative;
  }
  .card {
    position: absolute;
    width: 540px;
    height: 310px;
    background: var(--card);
    border-radius: 18px;
    box-shadow: 0 3px 0 var(--card-edge), 0 6px 0 #cfcfce, 0 12px 24px rgba(60, 45, 30, 0.25);
  }
  .card--front { left: 90px; top: 110px; }
  .card--back { left: 570px; top: 510px; }

  .brand-mark {
    display: flex;
    align-items: center;
    gap: 12px;
    color: var(--brand-grey);
    font-weight: 700;
    text-transform: uppercase;
    letter-spacing: 0.5px;
    white-space: nowrap;
  }
  .brand-mark__dot {
    width: 18px; height: 18px;
    background: var(--brand-brown);
    border-radius: 50%;
    flex: none;
  }
  .card--front .brand-mark {
    position: absolute;
    left: 0; right: 0; top: 134px;
    justify-content: center;
    font-size: 34px;
  }
  .card--back .brand-mark {
    position: absolute;
    right: 32px; top: 118px;
    font-size: 21px;
    gap: 8px;
  }
  .card--back .brand-mark__dot { width: 12px; height: 12px; }

  .details {
    position: absolute;
    left: 40px; top: 82px;
    color: var(--ink);
  }
  .details__company {
    font-size: 22px;
    font-weight: 700;
    color: var(--brand-brown);
    margin-bottom: 20px;
  }
  .details__name {
    font-size: 20px;
    text-transform: uppercase;
    letter-spacing: 0.5px;
  }
  .details__role {
    font-size: 17px;
    font-weight: 700;
    color: var(--brand-brown);
    margin-bottom: 12px;
  }
  .contact { list-style: none; }
  .contact__item {
    display: flex;
    align-items: center;
    gap: 10px;
    font-size: 17px;
    letter-spacing: 0.4px;
    line-height: 26px;
    white-space: nowrap;
  }
  .contact__icon { width: 18px; height: 16px; flex: none; }
</style>
</head>
<body>
  <section class="card card--front" aria-label="Card front">
    <div class="brand-mark"><span class="brand-mark__dot"></span>Talbert Stonecraft</div>
  </section>

  <section class="card card--back" aria-label="Card back">
    <div class="details">
      <p class="details__company">Talbert Stonecraft</p>
      <p class="details__name">Mara Voss</p>
      <p class="details__role">Director</p>
      <ul class="contact">
        <li class="contact__item">
          <svg class="contact__icon" viewBox="0 0 18 16" aria-hidden="true">
            <path d="M1 5 Q9 0 17 5 L15 7 L12 5.5 L6 5.5 L3 7 Z" fill="var(--icon)"/>
            <rect x="4" y="8" width="10" height="7" rx="1.5" fill="var(--icon)"/>
            <circle cx="9" cy="11.5" r="1.8" fill="var(--card)"/>
          </svg>
          555-302-4718
        </li>
        <li class="contact__item">
          <svg class="contact__icon" viewBox="0 0 18 16" aria-hidden="true">
            <rect x="1" y="3" width="16" height="11" fill="var(--icon)"/>
            <path d="M1 3 L9 10 L17 3" fill="none" stroke="var(--card)" stroke-width="1.4"/>
          </svg>
          Talbertstonecraft@mailbrook.net
        </li>
        <li class="contact__item">
          <svg class="contact__icon" viewBox="0 0 18 16" aria-hidden="true">
            <rect x="1.5" y="1.5" width="15" height="10" fill="none" stroke="var(--icon)" stroke-width="1.5"/>
            <circle cx="9" cy="6.5" r="2.4" fill="none" stroke="var(--icon)" stroke-width="1.1"/>
            <rect x="6" y="13" width="6" height="2" fill="var(--icon)"/>
          </svg>
          www.talbertstonecraft.net
        </li>
      </ul>
    </div>
    <div class="brand-mark"><span class="brand-mark__dot"></span>Talbert Stonecraft</div>
  </section>
</body>
</html>
```